Camp Thornbrook 2021 Magazine Design

We are for someone to design our annual magazine/newsletter. This is a print newsletter that is a total of 20 pages. It will need to be designed in a way that is easy to share with our printers. The designer will need to be someone who is creative and easy to work with.
For those interested in this project we ask that you design 4 to 6 pages for us to view. Once we select the designer we will want the rest created in a two-week time span. For those submitting a bid please include front cover, theme & dates, mission & vision, and Make the Difference.

This link will provide the layout of the newsletter https://files.parcelvault.example/doc/7qzRk2LmVt9XwPa4NbHc6DsYe3FuJg8KoTiW5rQx/edit?share=1.

This link will provide you with the pictures that are needed and a few documents https://files.parcelvault.example/folders/4TpWx8QnRb2ZyLc7MfVd5HsJ?share=1

Details:
20 pages long (including covers)
8.5 x 11

Please message me if you need any further details.

Target Market(s)

Our alumni base. Covers all ages

Requirements
Must have
• Spelled out in document
Nice to have
• Spelled out in document
Should not have
• Spelled out in document

```html
<!DOCTYPE html>
<html lang="en">
<head>
<meta charset="utf-8">
<title>Camp Thornbrook — Mission, Vision &amp; Core Values</title>
<link href="https://fonts.googleapis.com/css2?family=Fira+Sans:ital,wght@0,400;0,600;0,700;1,700&display=swap" rel="stylesheet">
<style>
  :root {
    --paper: #ffffff;
    --ink: #1c1c1c;
    --orange: #f29d5f;
    --forest: #1f2b25;
    --green: #0b8a59;
    --teal: #6fd6c6;
    --teal-soft: #a6e6d6;
    --photo-grass: #7fae4e;
    --photo-sky: #dff0ef;
  }
  * { box-sizing: border-box; margin: 0; padding: 0; }
  html, body { width: 1200px; height: 776px; overflow: hidden; background: var(--paper); }
  body { font-family: "Fira Sans", sans-serif; color: var(--ink); }
  .spread { position: relative; width: 1200px; height: 776px; overflow: hidden; }

  .photo { position: absolute; }
  .photo-cross {
    left: 0; top: 0; width: 600px; height: 435px;
    background: linear-gradient(180deg, #5d7a3c 0%, #8fb35e 45%, var(--photo-grass) 100%);
  }
  .photo-gate {
    left: 600px; top: 340px; width: 600px; height: 436px;
    background: linear-gradient(180deg, var(--photo-sky) 0%, #bcd9b0 30%, #5f8f3f 60%, #2f9a55 100%);
  }

  .headline {
    position: absolute; left: 20px; top: 443px; width: 428px; height: 58px;
    background: var(--orange); padding: 6px 8px 0 9px;
    font-style: italic; font-weight: 700; font-size: 18.2px; line-height: 21px; color: #1d1d1d;
  }

  .body-col {
    position: absolute; top: 516px; width: 262px;
    font-size: 10.6px; line-height: 11.75px; color: #222;
  }
  .body-col.one { left: 29px; }
  .body-col.two { left: 305px; }
  .dropcap {
    float: left; font-size: 38px; line-height: 30px; margin: 1px 3px 0 -1px; font-weight: 400;
  }
  .body-col p + p { text-indent: 3px; }

  .panel { position: absolute; text-align: center; }
  .panel h2 { font-weight: 700; font-size: 18.5px; line-height: 22px; }
  .vision {
    left: 628px; top: 21px; width: 261px; height: 132px; background: var(--orange);
    padding-top: 11px; color: #1e2a24;
  }
  .vision li { list-style: none; font-size: 10.2px; line-height: 17.4px; }
  .vision ul { margin-top: 3px; }
  .mission {
    left: 911px; top: 21px; width: 261px; height: 132px; background: var(--forest);
    padding: 11px 6px 0; color: var(--teal);
  }
  .mission p { font-size: 10.2px; line-height: 11.9px; margin-top: 3px; }
  .values {
    left: 628px; top: 161px; width: 544px; height: 186px; background: var(--green);
    padding: 4px 70px 0; color: var(--teal-soft);
  }
  .values h2 { color: var(--teal); }
  .values li { list-style: none; font-size: 10.2px; line-height: 11.8px; margin-top: 5.3px; }
</style>
</head>
<body>
<main class="spread">
  <div class="photo photo-cross" role="img" aria-label="Photo of a rustic wooden cross set on a tree stump in a sunlit, grassy wooded camp area"></div>

  <div class="headline">our new mission statement, we’ve made<br>“Encountering Christ, Community, and Creation”</div>

  <div class="body-col one">
    <p><span class="dropcap">L</span>ast year, we were asked by another camp director, “What is your mission statement?” We knew what we did at Camp Thornbrook, but didn’t really know how to efficiently describe what &nbsp;the mission looked like. This led to some self evaluation of our mission, vision, and core values.</p>
    <p>You may have noticed that we have been putting “Christ - Community - Creation” on everything. It’s on our new logo, it’s on almost all of our social media posts, at the end of our emails, and on all of our materials that we send out through the mail. We decided that those three things were the heart of the Thornbrook experience. This self evaluation led to the creation of our mission statement: “We want to strengthen young people’s relationship with Christ through meaningful worship experiences, create an environment that promotes community through Christ-centered relationships, and provide opportunities to experience God’s presence through His creation.”</p>
  </div>
  <div class="body-col two">
    <p>Because of our new mission statement, we’ve made “Encountering Christ, Community, and Creation” our vision statement and tagline in hopes to help continue to promote a culture that we have all experienced and grown to love and know during our time together at Thornbrook. Our hope is that through the direction and guidance of our mission, vision, and core value statements, we will continue to carry on the legacy of mission that so many have experienced on the grounds at camp.</p>
  </div>

  <section class="panel vision">
    <h2>Our Vision</h2>
    <ul>
      <li>Encountering Christ</li>
      <li>Encountering Community</li>
      <li>Encountering Creation</li>
    </ul>
  </section>

  <section class="panel mission">
    <h2>Our Mission</h2>
    <p>We want to strengthen young people’s relationship with Christ through meaningful worship experiences, create an environment that promotes community through Christ-centered relationships, and provide opportunities to experience God’s presence through His creation.</p>
  </section>

  <section class="panel values">
    <h2>Core Values</h2>
    <ul>
      <li>We believe camp ministry to be a highly effective way to minister to young people.</li>
      <li>We teach Biblical truth in love.</li>
      <li>We provide leadership and ministry opportunities for our counselors and staff members.</li>
      <li>We believe that the summer camp experience provides opportunities for creating and strengthening lifelong Christ centered relationships.</li>
      <li>We believe that the glory of God can be seen and experienced through His creation in nature.</li>
      <li>We believe it is important to bring glory to God by being good stewards of the gifts given to the mission of Camp Thornbrook.</li>
      <li>We want to provide the best experience possible for a reasonable price.</li>
    </ul>
  </section>

  <div class="photo photo-gate" role="img" aria-label="Photo of two campers in green shirts seen from behind, arm in arm, looking up at the camp entrance gate with trees beyond"></div>
</main>
</body>
</html>
```